Bright, captive yard sign for a roofing company used for marketing to potential customers.

I need a yard sign for my roofing company. I am looking for something that will catch peoples eyes as they are driving by.

The most important thing to me is that the lettering is visible and that the company and phone number are the two things that pop the most.

I want the yard sign to be the blue color and the lettering to be in black, or a black sign with white lettering and blue logo.

The sign will be 18x24 and a plastic type material.

Looking for something that is bright and eye catching but at the same time is simple and clear.

Target Market(s)

homeowners that are leaving near a job that we are doing or have just completed.

Industry/Entity Type

Roofing

Font styles to use
Serif

Colors
33a6d7

Requirements
Must have
• Must have the company name and logo.
• The phone number 602 - 415 - 3360
• email address Pinecresttopsaz.com
• Also must have "roc # 517094" on the sign but in a smaller not very visible area
Nice to have
• I would like to have "Roofing Experts, Insurance Claims Specialists" on the sign

```html
<!DOCTYPE html>
<html lang="en">
<head>
<meta charset="utf-8">
<title>Pinecrest Roofing – Yard Sign</title>
<link rel="stylesheet" href="https://fonts.googleapis.com/css2?family=Lato:wght@400;700;900&display=swap">
<style>
  :root {
    --backdrop: #4a4a4a;
    --sign-black: #221e1f;
    --brand-blue: #05a9e8;
    --white: #ffffff;
    --roc-tint: #e3f5fd;
    --ink: #111111;
  }
  * { margin: 0; padding: 0; box-sizing: border-box; }
  html, body {
    width: 1200px; height: 1200px; overflow: hidden;
    background: var(--backdrop);
    font-family: "Lato", sans-serif;
  }
  .yard-sign {
    position: absolute; left: 210px; top: 80px;
    width: 780px; height: 1040px;
    background: var(--sign-black);
    overflow: hidden;
    box-shadow: 0 6px 18px rgba(0,0,0,.35);
  }
  .brand-lockup {
    position: absolute; left: 0; right: 0; top: 120px;
    display: flex; align-items: center; justify-content: center; gap: 28px;
  }
  .brand-dot {
    width: 96px; height: 96px; border-radius: 50%;
    background: var(--brand-blue);
  }
  .brand-name {
    color: var(--white); font-weight: 700;
    font-size: 64px; line-height: 1.02; letter-spacing: 1px;
  }
  .headline {
    position: absolute; left: 124px;
    color: var(--brand-blue); font-weight: 700;
    font-size: 132px; line-height: 1; letter-spacing: -2px;
  }
  .headline--roofing { top: 400px; }
  .headline--experts { top: 518px; }
  .subline {
    position: absolute; left: 132px; color: var(--white); font-weight: 700; line-height: 1;
  }
  .subline--claims { top: 632px; font-size: 56px; letter-spacing: 0.5px; }
  .subline--specialists { top: 690px; font-size: 90px; letter-spacing: 1px; }
  .contact-band {
    position: absolute; left: 0; right: 0; top: 848px; bottom: 0;
    background: var(--brand-blue);
  }
  .phone-row {
    position: absolute; left: 126px; top: 822px;
    display: flex; align-items: center; gap: 22px;
  }
  .phone-icon { width: 56px; height: 56px; }
  .phone-pill {
    background: var(--white); color: var(--ink);
    font-weight: 700; font-size: 54px; line-height: 56px;
    padding: 0 16px; border-radius: 28px; letter-spacing: -0.5px;
  }
  .web-row {
    position: absolute; left: 124px; top: 920px;
    display: flex; align-items: center; gap: 14px;
    color: var(--white); font-weight: 700; font-size: 37px; letter-spacing: 1px;
  }
  .globe-icon { width: 32px; height: 32px; }
  .roc-number {
    position: absolute; left: 0; width: 718px; top: 992px; text-align: center;
    color: var(--roc-tint); font-weight: 400; font-size: 28px;
  }
</style>
</head>
<body>
  <main class="yard-sign">
    <div class="brand-lockup">
      <span class="brand-dot"></span>
      <div class="brand-name">PINECREST<br>ROOFING</div>
    </div>

    <h1 class="headline headline--roofing">ROOFING</h1>
    <div class="headline headline--experts">EXPERTS</div>
    <div class="subline subline--claims">INSURANCE CLAIMS</div>
    <div class="subline subline--specialists">SPECIALISTS</div>

    <div class="contact-band"></div>

    <div class="phone-row">
      <svg class="phone-icon" viewBox="0 0 56 56" aria-hidden="true">
        <circle cx="28" cy="28" r="25" fill="none" stroke="#fff" stroke-width="3"/>
        <path d="M20 15c2-1 3 0 4 2l2 5c.5 1.5 0 2.5-1 3.3l-1.5 1.2c1.5 3.5 4 6 7.5 7.5l1.2-1.5c.8-1 1.8-1.5 3.3-1l5 2c2 1 3 2 2 4-1.5 3-4 4.5-7 4-9-1.5-16-8.5-17.5-17.5-.5-3 1-5.5 2-9z" fill="#fff"/>
      </svg>
      <span class="phone-pill">602-415-3360</span>
    </div>

    <div class="web-row">
      <svg class="globe-icon" viewBox="0 0 32 32" aria-hidden="true" fill="none" stroke="#fff" stroke-width="2">
        <circle cx="16" cy="16" r="13"/>
        <ellipse cx="16" cy="16" rx="6" ry="13"/>
        <line x1="3" y1="16" x2="29" y2="16"/>
        <path d="M5.5 9h21M5.5 23h21"/>
      </svg>
      <span>Pinecresttopsaz.com</span>
    </div>

    <div class="roc-number">ROC # 517094</div>
  </main>
</body>
</html>
```